physio rehab flyer for Vela Mend please

Specification:
Flyer is to be trifold from letter size (8.5 x 11)
-----------------------This may help you:--------------------------
I would like the look of :
clean, minimalistic look with mainly blue and green
san serif font
professional
The colors I like are blue (not the blue in the logo enclosed, I want a change, but more like the blue on my website logo) and light green.
This is my website: www.velamendgroup.ca just so you get an idea but it will be totally changed soon to a to be determined design.
I like the blue and green in file "sample 2" (enclosed)
I like the pictures in "sample 2" file enclosed
For inspiration, I like design of this brochure: http://www.brelford.ca/HarlowRehab/PatientsFamilies/Clinics_Tests/DKAP_Service/Documents/Brochure.pdf
Here's how I see the pages layout:
----[location: this should be the cover (outside, right panel of trifold)]-----
Vela Mend Logo
Integrated Injury Rehab
Evidence-based, one-on-one care to make your recovery fast and comfortable
www.velamendgroup.ca
---------------[location: inside, left panel]----------------------------------------
Our team leaders
[portrait here]
Harriet Olsavik, MD, FRCPC, MSC, CIME
Physiatrist
Dr. Olsavik specializes in injury rehab and sports medicine. She is highly trained having received her MD and Residency in Physiatry from Pellham Institute. Her passion is to help injured people get back to their life.
[portrait here]
Wendy Carstairs, PT
Physiotherapist
Wendy has over 10 years of experience as a Physiotherapist (5 in Canada). She has advanced training in orthopedics and manual therapy. She loves and relates well with people from the youngest to the most senior.
--------------------[location: inside, middle panel]-------------------------------
Our services
We provide integrated assessment and care from interprofessional team of regulated healthcare professionals with proven experience in injury rehabilitation:
physiatrists
sport medicine physicians
physiotherapists
chiropractors
massage therapists
acupuncturists
psychologists
We provide custom medical bracing, orthotics, orthopedic shoes, assistive devices, and medical stockings, all in one place.
----------------------[location: inside, right panel]-----------------------------------
Only registered physiotherapists
We strongly believe in consistency with your treatment plan. This means that you spend your time here one-on-one with your physiotherapist, not any students or assistants. You get consistent high quality care from a professional.
One-on-one attention
We book maximum 3 people per hour to ensure everyone gets adequate one-on-one time with their physiotherapist. This compares favorably with other clinics, who may book upwards of 5-6 per hour. The atmosphere is professional -balanced with friendly, caring and relaxed. Our highly qualified staff operate this way to help make your recovery faster and more enjoyable.
------------------------[location: outside, left panel]---------------------------------
The right rehab for your clients
Timely access to comprehensive assessment and treatment
Proven track record in injury rehabilitation
Convenient one-stop service
Customized treatment plans
Integrated, co-ordinated care
Evidence-based care applying leading best practices
Access to specialty clinics: Physiatry and Chronic Pain
-------------------------[location: outside, middle panel]--------------------------
Please call us 555-384-2096
for more information on injury rehabilitation
Vela Mend Group
1862 Wexmoor Rd., Unit 9
Scarborough, ON K4T 8B2
[Please include a line art map designed based on "map" file enclosed]
To make a referral for your clients, contact velamendgroup@corvamail.ca or fax: 555-384-2071. Thank you.
www.velamendgroup.ca
------------------------------------------------------------------------------------------------
Target Market(s)
family doctors, ER docs, lawyers, and general public age (20-50)
Industry/Entity Type
Health And Wellness
Requirements
Must have
- san serif font
- blue and green colors
- clean, sophisticated look
Nice to have
- consumer choice award badge either on front or back of trifold
- see above

```html
<!DOCTYPE html>
<html lang="en">
<head>
<meta charset="utf-8">
<title>Vela Mend – Integrated Injury Rehab</title>
<link href="https://fonts.googleapis.com/css2?family=Open+Sans:wght@400;600;700;800&family=Libre+Baskerville:ital@1&display=swap" rel="stylesheet">
<style>
  :root {
    --blue: #5686c6;
    --blue-text: #4a7dbf;
    --green: #5e9e3a;
    --green-light: #8cc56a;
    --ink: #2e2e2e;
    --white: #ffffff;
    --navy: #27357a;
  }
  * { margin: 0; padding: 0; box-sizing: border-box; }
  html, body { width: 1200px; height: 928px; overflow: hidden; background: var(--white); }
  body { font-family: "Open Sans", Arial, sans-serif; color: var(--ink); }

  .flyer { position: relative; width: 1200px; height: 928px; display: flex; }
  .panel { position: relative; width: 400px; height: 928px; overflow: hidden; }

  /* Left panel: referral benefits */
  .benefits { background: var(--white); }
  .benefits-title {
    position: absolute; left: 20px; top: 32px; z-index: 2;
    font-size: 22px; font-weight: 400; color: var(--green);
  }
  .benefits-rule {
    position: absolute; left: 14px; top: 66px; width: 374px; height: 3px; z-index: 2;
    background: linear-gradient(90deg, var(--green), var(--green-light));
  }
  .benefit-list { list-style: none; position: absolute; inset: 0; z-index: 2; }
  .benefit {
    position: absolute; left: 49px; width: 335px;
    font-size: 15px; line-height: 22px; color: var(--ink);
  }
  .benefit .tick { position: absolute; left: -28px; top: 2px; width: 18px; height: 16px; }
  .benefits-photo {
    position: absolute; left: 0; top: 470px; width: 400px; height: 445px; z-index: 1;
    background: linear-gradient(180deg, #ffffff 0%, #ffffff 16%, #eef1f0 30%, #d8cabd 50%, #c2a893 62%, #6f8f94 82%, #4f6e75 100%);
  }
  .benefits-band {
    position: absolute; left: 0; bottom: 0; width: 400px; height: 13px; z-index: 2;
    background: linear-gradient(90deg, var(--green), var(--green-light));
  }

  /* Middle panel: contact */
  .contact { background: var(--blue); color: var(--white); text-align: center; }
  .contact-mark {
    position: absolute; left: 154px; top: 14px; width: 100px; height: 96px;
    background: var(--white); display: flex; align-items: center; justify-content: center;
    font-size: 21px; font-weight: 800; line-height: 22px; color: var(--navy);
  }
  .contact-title {
    position: absolute; left: 0; top: 122px; width: 400px;
    font-size: 22px; font-weight: 400;
  }
  .contact-rule { position: absolute; left: 12px; top: 154px; width: 376px; height: 2px; background: rgba(255,255,255,.85); }
  .contact-call { position: absolute; left: 0; top: 170px; width: 400px; font-size: 15px; }
  .contact-call strong { font-size: 19px; font-weight: 700; margin-left: 6px; }
  .contact-info { position: absolute; left: 0; top: 209px; width: 400px; font-size: 15px; }
  .contact-address {
    position: absolute; left: 26px; top: 265px; font-style: normal;
    font-size: 15px; line-height: 23px; text-align: left;
  }
  .contact-map {
    position: absolute; left: 34px; top: 353px; width: 318px; height: 250px;
    background: #eef1f7; border: 3px solid var(--white);
  }
  .contact-referral { position: absolute; left: 0; top: 669px; width: 400px; font-size: 15px; line-height: 23px; }
  .contact-referral strong { font-weight: 700; }
  .contact-thanks {
    position: absolute; left: 0; top: 755px; width: 400px;
    font-family: "Libre Baskerville", Georgia, serif; font-style: italic; font-size: 32px;
  }
  .contact-web { position: absolute; left: 0; top: 854px; width: 400px; font-size: 14px; }

  /* Right panel: cover */
  .cover { background: var(--white); }
  .cover-name {
    position: absolute; left: 52px; top: 40px; width: 320px;
    font-size: 84px; font-weight: 800; line-height: 92px; color: #111;
  }
  .cover-tagline {
    position: absolute; left: 0; top: 318px; width: 400px; text-align: center;
    font-size: 18px; color: var(--blue-text);
  }
  .cover-photo { position: absolute; left: 0; top: 355px; width: 400px; height: 470px; }
  .cover-promise {
    position: absolute; left: 13px; top: 796px;
    font-size: 15px; line-height: 23px; color: var(--green);
  }
  .cover-band {
    position: absolute; left: 0; top: 855px; width: 400px; height: 43px;
    background: var(--green); color: var(--white);
    font-size: 20px; text-align: center; line-height: 43px;
  }
</style>
</head>
<body>
<main class="flyer">

  <section class="panel benefits">
    <h2 class="benefits-title">The right rehab for your clients</h2>
    <div class="benefits-rule"></div>
    <div class="benefits-photo" role="img" aria-label="Physiotherapist stretching a patient's shoulder and arm"></div>
    <ul class="benefit-list">
      <li class="benefit" style="top:128px"><svg class="tick" viewBox="0 0 18 16"><path d="M2 9 L7 14 L16 2" fill="none" stroke="#5e9e3a" stroke-width="3" stroke-linecap="round"/></svg>Timely access to comprehensive assessment and treatment</li>
      <li class="benefit" style="top:205px"><svg class="tick" viewBox="0 0 18 16"><path d="M2 9 L7 14 L16 2" fill="none" stroke="#5e9e3a" stroke-width="3" stroke-linecap="round"/></svg>Proven track record in injury rehabilitation</li>
      <li class="benefit" style="top:258px"><svg class="tick" viewBox="0 0 18 16"><path d="M2 9 L7 14 L16 2" fill="none" stroke="#5e9e3a" stroke-width="3" stroke-linecap="round"/></svg>Convenient one-stop service</li>
      <li class="benefit" style="top:307px"><svg class="tick" viewBox="0 0 18 16"><path d="M2 9 L7 14 L16 2" fill="none" stroke="#5e9e3a" stroke-width="3" stroke-linecap="round"/></svg>Customized treatment plans</li>
      <li class="benefit" style="top:356px"><svg class="tick" viewBox="0 0 18 16"><path d="M2 9 L7 14 L16 2" fill="none" stroke="#5e9e3a" stroke-width="3" stroke-linecap="round"/></svg>Integrated, co-ordinated care</li>
      <li class="benefit" style="top:407px"><svg class="tick" viewBox="0 0 18 16"><path d="M2 9 L7 14 L16 2" fill="none" stroke="#5e9e3a" stroke-width="3" stroke-linecap="round"/></svg>Evidence-based care applying leading best practices</li>
      <li class="benefit" style="top:481px"><svg class="tick" viewBox="0 0 18 16"><path d="M2 9 L7 14 L16 2" fill="none" stroke="#5e9e3a" stroke-width="3" stroke-linecap="round"/></svg>Access to specialty clinics: Physiatry<br>and Chronic Pain</li>
    </ul>
    <div class="benefits-band"></div>
  </section>

  <section class="panel contact">
    <div class="contact-mark">Vela<br>Mend</div>
    <h2 class="contact-title">Our Contact</h2>
    <div class="contact-rule"></div>
    <p class="contact-call">Please call us <strong>555-384-2096</strong></p>
    <p class="contact-info">for more information on injury rehabilitation</p>
    <address class="contact-address">Vela Mend Group<br>1862 Wexmoor Rd., Unit 9<br>Scarborough, ON K4T 8B2</address>
    <div class="contact-map" role="img" aria-label="Line map of the streets around the clinic location"></div>
    <p class="contact-referral">To make a referral for your clients, contact<br><strong>velamendgroup@corvamail.ca</strong> or fax: <strong>555-384-2071</strong>.</p>
    <p class="contact-thanks">Thank you!</p>
    <p class="contact-web">www.velamendgroup.ca</p>
  </section>

  <section class="panel cover">
    <h1 class="cover-name">Vela<br>Mend</h1>
    <p class="cover-tagline">Integrated Injury Rehab</p>
    <svg class="cover-photo" viewBox="0 0 400 470" role="img" aria-label="Therapist assessing a patient's knee and acupuncture treatment">
      <defs>
        <linearGradient id="cover-photo-tone" x1="0" y1="0" x2="1" y2="1">
          <stop offset="0" stop-color="#d9c2ad"/>
          <stop offset="0.45" stop-color="#a5785c"/>
          <stop offset="0.7" stop-color="#e8e4e0"/>
          <stop offset="1" stop-color="#f3ebe4"/>
        </linearGradient>
      </defs>
      <path d="M0 45 Q200 -5 400 8 L400 465 Q200 380 0 375 Z" fill="url(#cover-photo-tone)"/>
      <path d="M0 45 Q200 -5 400 8" fill="none" stroke="#5686c6" stroke-width="3"/>
      <path d="M0 375 Q200 380 400 465" fill="none" stroke="#5e9e3a" stroke-width="3"/>
    </svg>
    <p class="cover-promise">Evidence-based, one-on-one care to<br>make your recovery fast and comfortable</p>
    <div class="cover-band">www.velamendgroup.ca</div>
  </section>

</main>
</body>
</html>
```